Healthcare/Medical Consultant Company

QRN is a Healthcare Conultant Company. We help doctors manage the business side of their medical practice.
We already have a very basic world press design. We want an upgraded design that conveys partnership, healthcare expertise and healthcare innovation to our client. It needs to have a sleek, clean, modern and inclusive look. Pictures need need to convey diversity (including pictures of people of all races and shows both men and women working together in a healthcare environment to make it better). The Pictures on the home page should particularly illustrate diversity and Healthcare expertise. The company logo is blue and white but the site doesn’t have to follow the exact same theme but the logo needs to blend well with the chosen theme. The logo should ideally be in the header of the website. We would also like the following included in our website:

1. Pages should include: a home page, About Us page, Services page, Get a quote page, Contact Us page, Staff page(where we can add pictures and bio for staff).

2. The Drop down menu for services should have hyperlinks ( for each service)Leading to a page that provides detailed info about that specific service. Our services include: Revenue Cycle Management, Regulatory Compliance, Human Resources Management, & practice Management.

3. Links to social media should in the header or footer of each page.

4. Contact info should be in the footer of each page.

5. Clients should be an email to us from the contact page.

Target Market(s)

Physician Medical Practices

Industry/Entity Type

Medical

Coding

Coded - Design and coding required

Font styles to use
Sans Serif

Colors

Designer to choose colors to be used in the design.

Requirements
Must have
• See project description
Nice to have
• See project description

```html
<!DOCTYPE html>
<html lang="en">
<head>
<meta charset="utf-8">
<title>QRN Health Partners LLC</title>
<link href="https://fonts.googleapis.com/css2?family=Tinos:wght@400;700&family=Montserrat:wght@400;500;600&family=Open+Sans:wght@400;600&display=swap" rel="stylesheet">
<style>
:root{
  --blue:#2e9fd6;
  --blue-soft:#5bb6e2;
  --navy:#1d5a91;
  --ink:#333a40;
  --muted:#5c6166;
  --line:#d9dcdf;
  --grey-band:#eeeeef;
  --footer:#3a3d40;
  --white:#ffffff;
}
*{box-sizing:border-box;margin:0;padding:0}
html,body{width:1200px;height:3396px;overflow:hidden}
body{position:relative;background:var(--white);font-family:"Montserrat",Arial,sans-serif;color:var(--ink)}
.abs{position:absolute}
.serif{font-family:"Tinos","Times New Roman",serif;font-weight:700}
.btn{position:absolute;display:flex;align-items:center;justify-content:center;gap:12px;border-radius:26px;font-family:"Montserrat",sans-serif;font-weight:600;font-size:17px;letter-spacing:.5px;color:var(--white);background:var(--blue)}
.btn svg{width:22px;height:16px}

/* hero */
.hero{left:0;top:0;width:1200px;height:645px;overflow:hidden}
.hero-photo{position:absolute;inset:0;background:linear-gradient(110deg,#5f666c 0%,#8a9096 45%,#b9bec2 70%,#d4d7da 100%)}
.hero-overlay{position:absolute;inset:0}
.brand{display:flex;align-items:center;gap:12px;color:var(--white);font-family:"Montserrat",sans-serif;font-weight:600;font-size:20px;letter-spacing:.3px;white-space:nowrap}
.brand .dot{width:26px;height:26px;border-radius:50%;background:var(--blue);flex:none}
.hero .brand{left:80px;top:40px}
.nav{left:458px;top:44px;display:flex;font-size:15px;font-weight:500;color:var(--white)}
.nav a{color:var(--white);text-decoration:none;margin-right:28px}
.nav .active{padding-bottom:14px;border-bottom:2px solid var(--white)}
.quote{left:976px;top:31px;width:145px;height:46px;border:2px solid var(--white);border-radius:24px;color:var(--white);font-size:15px;font-weight:600;display:flex;align-items:center;justify-content:center;letter-spacing:.5px}
.hero-title{right:328px;top:244px;text-align:right;color:var(--white);font-size:46px;line-height:52px}

/* about */
.section-title{font-family:"Tinos",serif;font-weight:700;font-size:46px;line-height:50px;color:var(--blue);letter-spacing:.5px}
.section-title b{color:var(--navy)}
.about-title{left:80px;top:758px}
.copy{font-size:14px;line-height:24px;color:var(--muted)}
.about-copy{left:80px;top:814px;width:410px}
.about-copy p+p{margin-top:14px}

/* services */
.grey-band{left:0;top:1866px;width:1200px;height:530px}
.services{left:80px;top:1189px;width:1040px;height:736px;background:var(--blue)}
.services h2{position:absolute;left:0;width:100%;top:48px;text-align:center;color:var(--white);font-size:46px}
.service{position:absolute;width:457px;height:218px;background:var(--blue-soft);border-radius:4px;text-align:center;color:var(--white);padding:30px 36px 0}
.service h3{font-family:"Open Sans",sans-serif;font-weight:400;font-size:23px;margin-bottom:14px}
.service p{font-family:"Open Sans",sans-serif;font-size:13.5px;line-height:24px}
.service a{display:inline-block;margin-top:12px;color:var(--white);font-size:16px;font-weight:500;text-decoration:underline}
.explore{left:411px;top:652px;width:218px;height:47px;background:var(--white);color:var(--blue);font-weight:500}

/* contact */
.contact-title{left:80px;top:2020px}
.contact-copy{left:80px;top:2078px;width:480px}
.field{position:absolute;width:217px;height:46px;border:1.5px solid var(--line);border-radius:23px;background:var(--white);font-size:13.5px;color:var(--muted);padding-left:28px;display:flex;align-items:center}
.laptop{left:662px;top:2033px;width:538px;height:360px}

/* team */
.team-title{left:0;width:1200px;top:2466px;text-align:center}
.member{position:absolute;top:2533px;width:322px;height:406px;border:1.5px solid var(--line);background:var(--white);overflow:hidden;text-align:center}
.member .photo{position:absolute;left:0;top:0;width:100%;height:270px}
.member h4{position:absolute;top:292px;width:100%;font-weight:500;font-size:18px;color:var(--ink)}
.member p{position:absolute;top:330px;left:24px;right:24px;font-family:"Open Sans",sans-serif;font-size:14px;line-height:26px;color:var(--muted)}

/* footer */
.footer{left:0;top:3029px;width:1200px;height:304px;background:linear-gradient(100deg,#3c3f42,#4a4d50 50%,#3a3c3f);color:var(--white)}
.footer .brand{left:80px;top:96px}
.footer-email{left:80px;top:168px;width:288px;height:46px;border-bottom:1.5px solid rgba(255,255,255,.5);font-size:14px;display:flex;align-items:center;padding-left:6px}
.footer-email svg{position:absolute;right:10px;top:14px}
.footer h5{position:absolute;font-weight:600;font-size:20px;letter-spacing:.5px}
.links{position:absolute;list-style:none;font-size:13.5px}
.links li{height:39px;display:flex;align-items:center;gap:14px}
.links li::before{content:"";width:8px;height:8px;border-radius:50%;background:var(--blue)}
.info{position:absolute;left:801px;font-size:13.5px;line-height:24px;display:flex;gap:16px;align-items:flex-start}
.info svg{flex:none;margin-top:3px}
.bottom-bar{left:0;top:3333px;width:1200px;height:63px;background:var(--blue);color:var(--white)}
.bottom-bar .legal{position:absolute;left:80px;top:22px;font-size:13.5px}
.social{position:absolute;top:9px;width:45px;height:45px;border:1.5px solid var(--white);border-radius:50%;display:flex;align-items:center;justify-content:center}
</style>
</head>
<body>

<header class="abs hero">
  <div class="hero-photo" role="img" aria-label="Business team meeting in a bright modern office"></div>
  <svg class="hero-overlay" width="1200" height="645" viewBox="0 0 1200 645">
    <polygon points="0,0 1200,0 1200,645 0,645" fill="#1a2530" opacity=".25"/>
    <polygon points="747,645 1120,0 1200,0 1200,645" fill="#ffffff" opacity=".25"/>
    <line x1="747" y1="645" x2="1120" y2="0" stroke="#2e9fd6" stroke-width="5"/>
  </svg>
  <div class="abs brand"><span class="dot"></span>QRN Health Partners LLC</div>
  <nav class="abs nav">
    <a class="active" href="#">HOME</a><a href="#">ABOUT US</a><a href="#">SERVICES</a><a href="#">OUR STAFF</a><a href="#">CONTACT US</a>
  </nav>
  <div class="abs quote">GET A QUOTE</div>
  <h1 class="abs hero-title serif">QRN HEALTH<br>PARTNERS<br>LLC</h1>
  <div class="btn" style="left:706px;top:437px;width:206px;height:50px">KNOW MORE
    <svg viewBox="0 0 22 16"><path d="M1 8h19M13 1l7 7-7 7" fill="none" stroke="#fff" stroke-width="2.4"/></svg></div>
</header>

<section>
  <h2 class="abs section-title about-title">ABOUT <b>US</b></h2>
  <div class="abs copy about-copy">
    <p>Lorem Ipsum is simply dummy text of the printing and typesetting industry. Lorem Ipsum has been the industry's standard dummy text ever since the 1500s, when an unknown printer took a galley of type and scrambled it to make a type specimen book.</p>
    <p>It has survived not only five centuries, but also the leap into electronic typesetting, remaining essentially.</p>
  </div>
  <div class="btn" style="left:80px;top:1021px;width:197px;height:48px">KNOW MORE
    <svg viewBox="0 0 22 16"><path d="M1 8h19M13 1l7 7-7 7" fill="none" stroke="#fff" stroke-width="2.4"/></svg></div>
  <svg class="abs" style="left:560px;top:645px" width="640" height="590" viewBox="0 0 640 590" role="img" aria-label="Doctor and colleague reviewing work together at a laptop">
    <defs><linearGradient id="aboutFill" x1="0" y1="0" x2="1" y2="1"><stop offset="0" stop-color="#d8dde2"/><stop offset="1" stop-color="#a9b4bd"/></linearGradient></defs>
    <polygon points="6,544 232,8 640,0 640,588 300,556" fill="url(#aboutFill)"/>
  </svg>
</section>

<svg class="abs grey-band" width="1200" height="530" viewBox="0 0 1200 530">
  <polygon points="0,0 1200,0 1200,490 0,530" fill="#eeeeef"/>
</svg>

<section class="abs services">
  <h2 class="serif">OUR SERVICES</h2>
  <div class="service" style="left:40px;top:113px"><h3>Revenue Cycle Management</h3><p>Lorem Ipsum is simply dummy text of the printing and typesetting industry. Lorem Ipsum has been the industry's standard dummy text ever since the 1500s.</p><a href="#">READ MORE</a></div>
  <div class="service" style="left:543px;top:113px"><h3>Medical Billing &amp; Coding</h3><p>Lorem Ipsum is simply dummy text of the printing and typesetting industry. Lorem Ipsum has been the industry's standard dummy text ever since the 1500s.</p><a href="#">READ MORE</a></div>
  <div class="service" style="left:40px;top:373px"><h3>Regulatory Compliance</h3><p>Lorem Ipsum is simply dummy text of the printing and typesetting industry. Lorem Ipsum has been the industry's standard dummy text ever since the 1500s.</p><a href="#">READ MORE</a></div>
  <div class="service" style="left:543px;top:373px"><h3>Human Resources Training</h3><p>Lorem Ipsum is simply dummy text of the printing and typesetting industry. Lorem Ipsum has been the industry's standard dummy text ever since the 1500s.</p><a href="#">READ MORE</a></div>
  <div class="btn explore">EXPLORE MORE
    <svg viewBox="0 0 22 16"><path d="M1 8h19M13 1l7 7-7 7" fill="none" stroke="#2e9fd6" stroke-width="2.4"/></svg></div>
</section>

<section>
  <h2 class="abs section-title contact-title">CONTACT <b>US</b></h2>
  <p class="abs copy contact-copy">Please feel free to contact us at the information provided below and we will be sure to get back to you as soon as possible.</p>
  <div class="field" style="left:80px;top:2150px">Name</div>
  <div class="field" style="left:317px;top:2150px">Phone No.</div>
  <div class="field" style="left:80px;top:2212px">Email</div>
  <div class="field" style="left:317px;top:2212px">Message</div>
  <div class="btn" style="left:80px;top:2268px;width:197px;height:48px">SUBMIT NOW
    <svg viewBox="0 0 22 16"><path d="M1 8h19M13 1l7 7-7 7" fill="none" stroke="#fff" stroke-width="2.4"/></svg></div>
  <div class="abs laptop" role="img" aria-label="Laptop showing a diverse team collaborating around a table" style="background:linear-gradient(135deg,#2a2d31 0%,#4d6478 40%,#9fb6c8 70%,#c9ccd0 100%);border-radius:14px 0 0 6px"></div>
</section>

<section>
  <h2 class="abs section-title team-title">OUR <b>TEAM</b></h2>
  <article class="member" style="left:79px">
    <svg class="photo" viewBox="0 0 322 270" preserveAspectRatio="none" role="img" aria-label="Portrait of a smiling team member in a checked shirt"><polygon points="0,0 322,0 322,228 0,270" fill="#5d6266"/></svg>
    <h4>NAME SURNAME</h4><p>Lorem Ipsum is simply dummy text of the printing and typesetting industry.</p>
  </article>
  <article class="member" style="left:439px">
    <svg class="photo" viewBox="0 0 322 270" preserveAspectRatio="none" role="img" aria-label="Portrait of a team member in a dark blazer"><polygon points="0,0 322,0 322,228 0,270" fill="#8f99a2"/></svg>
    <h4>NAME SURNAME</h4><p>Lorem Ipsum is simply dummy text of the printing and typesetting industry.</p>
  </article>
  <article class="member" style="left:799px">
    <svg class="photo" viewBox="0 0 322 270" preserveAspectRatio="none" role="img" aria-label="Portrait of a smiling team member in a checked shirt"><polygon points="0,0 322,0 322,228 0,270" fill="#5d6266"/></svg>
    <h4>NAME SURNAME</h4><p>Lorem Ipsum is simply dummy text of the printing and typesetting industry.</p>
  </article>
</section>

<footer class="abs footer">
  <div class="abs brand"><span class="dot"></span>QRN Health Partners LLC</div>
  <div class="abs footer-email">Email
    <svg width="20" height="18" viewBox="0 0 20 18"><path d="M1 8 19 1 14 17 9 11Z M9 11 19 1" fill="none" stroke="#2e9fd6" stroke-width="1.8"/></svg></div>
  <h5 style="left:441px;top:66px">SITEMAP</h5>
  <ul class="links" style="left:441px;top:84px"><li>Home</li><li>About us</li><li>Services</li><li>Our Staff</li></ul>
  <ul class="links" style="left:597px;top:84px"><li>Get a quote</li><li>contact us</li><li>Terms of use</li><li>Privacy Policy</li></ul>
  <h5 style="left:801px;top:66px">CONTACT INFO</h5>
  <div class="info" style="top:102px;width:330px">
    <svg width="16" height="20" viewBox="0 0 16 20"><path d="M8 19S1 11 1 7a7 7 0 0 1 14 0c0 4-7 12-7 12Z" fill="#2e9fd6"/><circle cx="8" cy="7" r="2.6" fill="#3a3d40"/></svg>
    <span>Lorem Ipsum is simply dummy text of the printing and typesetting industry.</span></div>
  <div class="info" style="top:164px">
    <svg width="18" height="18" viewBox="0 0 18 18"><path d="M4 1 7 5 5 7c1 2 4 5 6 6l2-2 4 3-2 3C9 17 1 9 1 3Z" fill="#2e9fd6"/></svg>
    <span>123 456 7890</span></div>
  <div class="info" style="top:202px">
    <svg width="18" height="14" viewBox="0 0 18 14"><rect x="1" y="1" width="16" height="12" fill="none" stroke="#2e9fd6" stroke-width="1.8"/><path d="M1 1l8 6 8-6" fill="none" stroke="#2e9fd6" stroke-width="1.8"/></svg>
    <span>info@qrnhealthpartners.com</span></div>
</footer>

<div class="abs bottom-bar">
  <p class="legal">©QRN HEALTH PARTNERS LLC. 2018 - All Rights Reserved.</p>
  <span class="social" style="left:902px" aria-label="Share">
    <svg width="18" height="18" viewBox="0 0 18 18"><circle cx="4" cy="9" r="2.3" fill="#fff"/><circle cx="14" cy="4" r="2.3" fill="#fff"/><circle cx="14" cy="14" r="2.3" fill="#fff"/><path d="M4 9 14 4M4 9l10 5" stroke="#fff" stroke-width="1.5"/></svg></span>
  <span class="social" style="left:960px" aria-label="Chat">
    <svg width="18" height="18" viewBox="0 0 18 18"><path d="M2 3h14v9H8l-4 3v-3H2Z" fill="none" stroke="#fff" stroke-width="1.6" stroke-linejoin="round"/></svg></span>
  <span class="social" style="left:1018px" aria-label="Web">
    <svg width="18" height="18" viewBox="0 0 18 18"><circle cx="9" cy="9" r="7" fill="none" stroke="#fff" stroke-width="1.5"/><path d="M2 9h14M9 2c-3 4-3 10 0 14M9 2c3 4 3 10 0 14" fill="none" stroke="#fff" stroke-width="1.3"/></svg></span>
  <span class="social" style="left:1076px" aria-label="Mail">
    <svg width="18" height="14" viewBox="0 0 18 14"><rect x="1" y="1" width="16" height="12" fill="none" stroke="#fff" stroke-width="1.6"/><path d="M1 1l8 6 8-6" fill="none" stroke="#fff" stroke-width="1.6"/></svg></span>
</div>

</body>
</html>
```